I want ideas sample designs for my book cover

Hello,

We need a book cover designed in flat and 3D Versions. We would like to have jpg and png for final output and include a copy of the PSD for future revisions.

Here are the basic details:

Title: The Harvest of Quiet Builders
Author: Norman Quillfeather

Dimensions of book:

Was looking at the Pavo website for dimensions. I thought you may want to go on there and look at the different sizes. I used the 6x9” perfect bound US trade size for my book. You will see that this has a spine width of 0.225”, Cover size of 12.48 x 9.25” and spine begins at 6.125”

If you need background info on the author just to get an idea what he does, please check:

http://NormanQuillfeather.example

IMPORTANT: Please see attached document for a more detailed info:

Exact Title Of book
Back Cover
Spine Info
Measurements of book and dimension
Examples of book covers
Norman's photo attached

Thanks,
Darlene

Industry/Entity Type

Life Coaching

Font styles to use
Serif

Requirements
Must have
• Jpg, png and PSD files
• title
• author
• exact dimensions
• front and back cover
• flat and 3d versions

```html
<!DOCTYPE html>
<html lang="en">
<head>
<meta charset="utf-8">
<title>The Harvest of Quiet Builders — Cover Wrap</title>
<link href="https://fonts.googleapis.com/css2?family=Oswald:wght@400;500&family=Open+Sans:wght@400&family=Roboto+Condensed:wght@700&display=swap" rel="stylesheet">
<style>
  :root {
    --back-bg: #8ea5b8;
    --stripe: #1c3f70;
    --navy: #173d73;
    --navy-band: #1e4678;
    --spine-bg: #dfe6ec;
    --ink: #2b2f36;
    --white: #ffffff;
    --art-top: #1e3448;
    --art-mid: #6e8597;
    --art-low: #9fb0bb;
  }
  * { margin: 0; padding: 0; box-sizing: border-box; }
  html, body { width: 1200px; height: 890px; overflow: hidden; background: #fff; }
  .cover-wrap { position: relative; width: 1200px; height: 890px; overflow: hidden; }

  /* Back cover */
  .back-cover { position: absolute; left: 0; top: 0; width: 590px; height: 890px; background: var(--back-bg); }
  .back-stripe { position: absolute; left: 62px; top: 0; width: 84px; height: 890px; background: var(--stripe); }
  .back-url {
    position: absolute; left: 104px; top: 205px;
    transform: translate(-50%, -50%) rotate(-90deg);
    white-space: nowrap; color: var(--white);
    font-family: "Open Sans", sans-serif; font-size: 17px; letter-spacing: 0.2px;
  }
  .author-tab {
    position: absolute; left: 0; top: 390px; width: 181px; height: 129px;
    background: var(--navy); border-radius: 0 12px 12px 0;
    display: flex; flex-direction: column; justify-content: center; align-items: center;
    padding-left: 10px;
    color: var(--white); font-family: "Roboto Condensed", sans-serif; font-weight: 700;
    font-size: 24px; line-height: 1.15; letter-spacing: -0.3px; text-align: center;
  }
  .author-tab span:first-child { font-size: 33px; }
  .author-photo {
    position: absolute; left: 0; top: 620px; width: 210px; height: 270px;
    background: linear-gradient(160deg, #c9ced3 0%, #8f969c 45%, #e8eaec 100%);
    border-top-right-radius: 90px;
  }
  .back-copy {
    position: absolute; left: 205px; top: 60px; width: 350px;
    font-family: "Open Sans", sans-serif; font-size: 9.2px; line-height: 1.38;
    color: var(--ink); text-align: justify;
  }
  .back-copy p { margin-bottom: 11.5px; }
  .back-blank { position: absolute; left: 205px; top: 733px; width: 349px; height: 121px; background: var(--white); }

  /* Spine */
  .spine { position: absolute; left: 590px; top: 0; width: 22px; height: 890px; background: var(--spine-bg); }
  .spine-title {
    position: absolute; left: 11px; top: 448px;
    transform: translate(-50%, -50%) rotate(90deg);
    white-space: nowrap; color: var(--ink);
    font-family: "Open Sans", sans-serif; font-size: 15px; letter-spacing: 2.6px;
  }

  /* Front cover */
  .front-cover { position: absolute; left: 612px; top: 0; width: 588px; height: 890px; }
  .front-art {
    position: absolute; inset: 0;
    background: linear-gradient(180deg, var(--art-top) 0%, #3d566b 20%, var(--art-mid) 45%, var(--art-low) 85%, #aebdc5 100%);
  }
  .title-band { position: absolute; left: 0; top: 277px; width: 588px; height: 263px; background: var(--white); }
  .subtitle-band { position: absolute; left: 0; top: 540px; width: 588px; height: 82px; background: var(--navy-band); }
  .author-band { position: absolute; left: 0; top: 622px; width: 588px; height: 113px; background: var(--white); }
  .figure-slot {
    position: absolute; left: 440px; top: 250px; width: 115px; height: 555px;
    background: linear-gradient(180deg, #c9cfd6 0%, #7c8590 45%, #262a30 100%);
    border-radius: 50px 50px 8px 8px; opacity: 0.85;
  }
  .front-title {
    position: absolute; right: 185px; top: 300px; text-align: right; z-index: 2;
    font-family: "Oswald", sans-serif; font-weight: 500; color: var(--navy);
    font-size: 58px; line-height: 1.18; text-transform: uppercase; letter-spacing: -0.5px;
  }
  .subtitle {
    position: absolute; left: 62px; top: 540px; width: 380px; height: 82px; z-index: 2;
    display: flex; align-items: center; justify-content: center;
    text-align: center; color: var(--white);
    font-family: "Open Sans", sans-serif; font-size: 14px; line-height: 1.3;
  }
  .author-credit {
    position: absolute; right: 185px; top: 654px; z-index: 2; white-space: nowrap;
    font-family: "Roboto Condensed", sans-serif; font-weight: 700; font-size: 16px;
    color: var(--navy); text-transform: uppercase; letter-spacing: -0.2px;
  }
  .author-front {
    position: absolute; right: 185px; top: 676px; z-index: 2; white-space: nowrap;
    font-family: "Oswald", sans-serif; font-weight: 500; font-size: 38px;
    color: var(--navy); text-transform: uppercase; letter-spacing: -0.5px; line-height: 1.2;
  }
</style>
</head>
<body>
<main class="cover-wrap">

  <section class="back-cover">
    <div class="back-stripe"></div>
    <div class="back-url">www.NormanQuillfeather.example</div>
    <div class="author-tab"><span>NORMAN</span><span>QUILLFEATHER</span></div>
    <div class="author-photo" role="img" aria-label="Portrait photograph of the author in a white t-shirt"></div>

    <div class="back-copy">
      <p>This path goes way beyond Entrepreneurism! This is a book for the awakening Entrepreneurs who are building businesses for a better world, affecting generations to come. Bringing you disruptive (in a good way) information, to turn you and your business inside-out for maximum acceleration towards your organisational vision, mission and values.</p>
      <p>There is the potential to have a more meaningful life and business by discovering the symbiotic relationship that exists between all beings. You will be empowered to take your life and business to the next level if you answer the call in this book. It will introduce you to the power of Amazonian plant medicine and other entheogens for improving relationships with yourself, your partner and your family, friends, business associates and Mother Earth.</p>
      <p>An entheogen is defined as 'a substance (usually from a plant, but not always) that is consumed in order to alter one's state of consciousness or to act as a catalyst towards encounters with other states of being.' Plant medicine has been successfully used in South America for thousands of years. This ancient wisdom is helping billionaires, industry icons and entrepreneurs to be better leaders, awakening to its potential for allowing deep examination of the psyche which has the ability to heal, eliminate fears and create a new level of success both personally and professionally.</p>
      <p>Norman shares his own heart-felt personal experiences and insights gained from working with these substances and the amazing medicine men and women of the Amazon who retain thousands of years of ancient wisdom. He has spent years turning himself inside-out to powerfully transform his own life and business and wants to encourage entrepreneurs to do the same. He believes that if enough people have the opportunity to explore their own consciousness, then together we can make a positive impact on humanity. If you are ready to travel to the fringes and take a journey within, you will discover that you are the missing link you have been looking for. Get ready to expand your consciousness, transform your business and create a new inspiring lifestyle, which will benefit all beings and our beautiful Mother Earth.</p>
      <p>Norman Quillfeather is an internationally-renowned entrepreneur, speaker, philanthropist, thought leader and best-selling author. Having played the role of transformational coach, facilitator and spoken to over three million people from twelve different countries, he challenges you in his second book to journey deep within yourself to examine the core of your true nature and how it impacts your entrepreneurial journey. Some of the world biggest game changers, social entrepreneurs, internet marketers and consultants have reported that Norman's golden edge is to integrate "purpose with profits" in a way that brings greater meaning to the work they are doing here in the world.</p>
    </div>
    <div class="back-blank"></div>
  </section>

  <section class="spine">
    <div class="spine-title">THE HARVEST OF QUIET BUILDERS</div>
  </section>

  <section class="front-cover">
    <div class="front-art" role="img" aria-label="Chalkboard sketch of business ideas, clouds, charts and arrows over a misty floor"></div>
    <div class="title-band"></div>
    <div class="subtitle-band"></div>
    <div class="author-band"></div>
    <div class="figure-slot" role="img" aria-label="Businesswoman standing in profile holding a briefcase"></div>
    <h1 class="front-title">The Harvest<br>of Quiet<br>Builders</h1>
    <p class="subtitle">How this ancient wisdom is helping billionaires,<br>industry icons and entrepreneurs to be better<br>leaders, increase impact and leave a legacy.</p>
    <p class="author-credit">From the best selling author of “Lanterns”</p>
    <p class="author-front">Norman Quillfeather</p>
  </section>

</main>
</body>
</html>
```